Personalized Technology Company Needs a Business Card

I need a double-sided business card. Both sides will have the logo, and the contact information. One side will be black, with the white / gray logo, and the other will be white, with the black / gray logo. The black side will have the text "Custom Gaming PC's" and will have a water-cooled gaming PC image. The white side will have the text "Custom Business Computers & Consulting", and will have a business / enterprise PC image. Feel free to add a conservative image in the background, while the color remains unchanged. I'm uploading the base logo (transparent), so you can modify the colors, both the finished colored logos and an idea of ​​the business card (with the current information, just missing the website, which is www.velomindsystems.com, please add it.) Thank you so much for your effort, I'll be specting your cool designs. Good Luck!

Target Market(s)

Gamers & Entrepreneurs / Business Owners / Chief Technology Officers

Industry/Entity Type

Technology Equipment

Contact Information for Business Card

I need a double-sided business card. Both sides will have the logo, and the contact information. One side will be black, with the white/gray logo, and the other one will be white, with the black/gray logo. The black side will have the text "Custom Gaming PC's" and will have a water-cooled gaming PC image. The white side will have the text "Custom Business Computers & Consulting", and will have a business/enterprise PC image. Feel free to add a conservative image in the background, whilst the color remains unchanged.

I'm uploading the base logo (transparent), so you can modify the colors, both the finished colored logos and an idea of the business card (with the actual information, just missing the website, which is www.velomindsystems.com, please add it.)

Thank you so much for your effort, I'll be specting your cool designs. Good Luck!

Font styles to use
Serif

Colors
000000
757575
ffffff

Requirements
Must have
• Please See Description
Nice to have
• Please See Description
Should not have
• Please See Description

```html
<!DOCTYPE html>
<html lang="en">
<head>
<meta charset="utf-8">
<title>Velomind Systems — Business Card</title>
<link rel="stylesheet" href="https://fonts.googleapis.com/css2?family=Tinos:wght@400;700&display=swap">
<style>
  :root {
    --stage: #2a2a2c;
    --black: #000000;
    --ink: #0d0d0f;
    --grey: #757575;
    --white: #ffffff;
    --cream: #ece6dc;
    --stone: #bfb6a8;
    --paper: #e9e9ee;
    --accent: #3b55b5;
  }
  * { margin: 0; padding: 0; box-sizing: border-box; }
  html, body { width: 1200px; height: 800px; overflow: hidden; }
  body {
    background: var(--stage);
    font-family: "Tinos", "Times New Roman", serif;
    position: relative;
  }
  .card {
    position: absolute;
    top: 245px;
    width: 540px;
    height: 310px;
    overflow: hidden;
    box-shadow: 0 14px 30px rgba(0,0,0,.45);
  }
  .card--dark { left: 40px; background: var(--black); color: var(--white); }
  .card--light { left: 620px; background: var(--paper); color: var(--ink); }

  .backdrop { position: absolute; inset: 0; }
  .card--dark .backdrop {
    background: linear-gradient(135deg, #141418 0%, #23252b 45%, #0b0b0d 100%);
  }
  .card--light .backdrop {
    background: linear-gradient(135deg, #f4f4f8 0%, #dcdde4 50%, #eeeff3 100%);
  }

  .mascot {
    position: absolute;
    top: 14px;
    width: 200px;
    height: 240px;
    border-radius: 48% 52% 40% 60% / 42% 40% 60% 58%;
  }
  .card--dark .mascot { right: 40px; background: radial-gradient(circle at 45% 40%, var(--cream) 0%, #d8d0c3 70%, var(--stone) 100%); }
  .card--light .mascot { right: 30px; top: 22px; background: radial-gradient(circle at 45% 40%, #111 0%, #1b1b1d 65%, var(--stone) 100%); }

  .rule { position: absolute; left: 0; right: 0; height: 3px; background: var(--accent); }
  .band {
    position: absolute; left: 0; right: 0; bottom: 0;
    display: flex; align-items: center;
    letter-spacing: .06em; text-transform: uppercase;
  }
  .card--dark .rule { top: 263px; }
  .card--dark .band { height: 44px; background: var(--cream); color: var(--ink); padding-left: 30px; font-size: 16px; }
  .card--light .rule { top: 271px; }
  .card--light .band { height: 36px; background: var(--black); color: var(--white); justify-content: flex-end; padding-right: 30px; font-size: 14px; }

  .brand {
    position: absolute;
    display: flex; align-items: center; gap: 10px;
    text-transform: uppercase;
  }
  .brand__dot { width: 12px; height: 12px; border-radius: 50%; background: currentColor; flex: none; }
  .brand__text { display: flex; flex-direction: column; line-height: 1; }
  .brand__name { font-weight: 700; letter-spacing: .1em; }
  .brand__sub { font-weight: 700; letter-spacing: .32em; margin-top: 5px; }
  .card--dark .brand { left: 30px; top: 34px; color: var(--white); }
  .card--dark .brand__name { font-size: 28px; }
  .card--dark .brand__sub { font-size: 11px; }
  .card--light .brand { left: 60px; top: 108px; color: var(--ink); }
  .card--light .brand__name { font-size: 32px; }
  .card--light .brand__sub { font-size: 12px; }

  .person { position: absolute; left: 30px; top: 100px; }
  .person__name { font-size: 19px; font-weight: 700; }
  .person__role { font-size: 13px; color: #d6d6d6; margin-top: 2px; }

  .contacts { position: absolute; left: 30px; top: 152px; width: 250px; font-size: 13px; }
  .contacts__group { padding: 6px 0; border-top: 1px dotted #cfcfcf; }
  .contacts__group:first-child { border-top: none; padding-top: 0; }
  .contacts__row { display: flex; align-items: center; gap: 8px; line-height: 1.45; }
  .contacts__row svg { width: 12px; height: 12px; flex: none; }

  .web { position: absolute; left: 30px; bottom: 52px; display: flex; align-items: center; gap: 8px; font-size: 14px; }
  .social { display: flex; gap: 5px; }
  .social span { width: 16px; height: 16px; border-radius: 50%; background: var(--ink); }
</style>
</head>
<body>

<section class="card card--dark" aria-label="Card front, dark side">
  <div class="backdrop" role="img" aria-label="Dim photo of a water-cooled gaming PC interior"></div>
  <div class="mascot" role="img" aria-label="Cream wolf head illustration"></div>

  <div class="brand">
    <span class="brand__dot"></span>
    <span class="brand__text"><span class="brand__name">Velomind</span><span class="brand__sub">Systems</span></span>
  </div>

  <div class="person">
    <p class="person__name">Marco Reyes Lund</p>
    <p class="person__role">(CEO &amp; Co-Founder)</p>
  </div>

  <div class="contacts">
    <div class="contacts__group">
      <p class="contacts__row">
        <svg viewBox="0 0 12 12"><path d="M3 1h2l1 3-1.5 1a6 6 0 0 0 2.5 2.5L8 6l3 1v2a2 2 0 0 1-2 2A8 8 0 0 1 1 3a2 2 0 0 1 2-2z" fill="#fff"/></svg>
        +52 5581 - 3092
      </p>
      <p class="contacts__row">
        <svg viewBox="0 0 12 12"><rect x="3" y="1" width="6" height="10" rx="1" fill="none" stroke="#fff"/><circle cx="6" cy="9" r=".8" fill="#fff"/></svg>
        +52 55 - 4816 - 7305
      </p>
    </div>
    <div class="contacts__group">
      <p class="contacts__row">
        <svg viewBox="0 0 12 12"><rect x="1" y="2.5" width="10" height="7" fill="none" stroke="#fff"/><path d="M1 2.5l5 4 5-4" fill="none" stroke="#fff"/></svg>
        contact@velomindsystems.com
      </p>
      <p class="contacts__row">
        <svg viewBox="0 0 12 12"><circle cx="6" cy="6" r="5" fill="none" stroke="#fff"/><path d="M1 6h10M6 1c-3 3-3 7 0 10M6 1c3 3 3 7 0 10" fill="none" stroke="#fff" stroke-width=".8"/></svg>
        www.velomindsystems.com
      </p>
    </div>
  </div>

  <div class="rule"></div>
  <p class="band">Custom Gaming PC's</p>
</section>

<section class="card card--light" aria-label="Card back, light side">
  <div class="backdrop" role="img" aria-label="Soft photo of a business workstation setup"></div>
  <div class="mascot" role="img" aria-label="Black wolf head illustration"></div>

  <div class="brand">
    <span class="brand__dot"></span>
    <span class="brand__text"><span class="brand__name">Velomind</span><span class="brand__sub">Systems</span></span>
  </div>

  <div class="web">
    <div class="social" aria-hidden="true"><span></span><span></span><span></span></div>
    www.velomindsystems.com
  </div>

  <div class="rule"></div>
  <p class="band">Custom Business Computers &amp; Consulting</p>
</section>

</body>
</html>
```